New business card for a regional office of a US M&A company

We need business card for a finance company, office based in Hong Kong , our Head office is in US, our business is to Merge and acquires companies , the new office will be a regional office for the Asia Pacific region. We want to use the head office logo as attached ( but don't have to be exactly the same, can be a variation to it) as a base and then add Asia Pacific alongside the logo.
We would prefer to have be bilingual Eng + Chinese, although we don't really have Chinese company name .

Industry/Entity Type

Business

Contact Information for Business Card

Clara Jo Tsang
 

VP,
APAC M&A Operations
Eli Global Asia Pacific Limited
 
Unit 1407, K18
18 Tai Lok Shan Road, 
Hong Kong 
 
M: +852 6038 1742
T : +852 2836 4100
F : +852 2836 4177
VOIP: 4158
 
cjtsang@orinvantage.com

Font styles to use
Serif
Sans Serif

Colors

Designer to choose colors to be used in the design.

Requirements
Must have
• APAC Office

```html
<!DOCTYPE html>
<html lang="en">
<head>
<meta charset="utf-8">
<title>Orin Vantage Asia Pacific – Business Card</title>
<link rel="stylesheet" href="https://fonts.googleapis.com/css2?family=Open+Sans:wght@400;600;700&display=swap">
<style>
  :root {
    --backdrop: #e6e7e9;
    --card: #fbfbfb;
    --navy: #0f2d4a;
    --cyan: #1ea2d6;
    --grey: #5a5d61;
    --ink: #1c2430;
    --rule: #d9dadc;
  }
  * { box-sizing: border-box; margin: 0; padding: 0; }
  html, body {
    width: 1200px; height: 900px; overflow: hidden;
    background: var(--backdrop);
    font-family: "Open Sans", Arial, sans-serif;
  }
  .canvas {
    position: relative; width: 1200px; height: 900px;
    display: flex; align-items: center; justify-content: center; gap: 50px;
  }
  .card {
    position: relative; width: 500px; height: 290px;
    background: var(--card); border-radius: 22px;
    box-shadow: 0 2px 10px rgba(0,0,0,0.12);
  }
  /* contact side */
  .card-contact .brand-block {
    position: absolute; left: 40px; top: 60px; width: 170px;
    display: flex; flex-direction: column; align-items: center; gap: 14px;
  }
  .brand-square {
    width: 110px; height: 110px; background: var(--navy);
  }
  .brand-caption {
    color: var(--navy); font-weight: 700; font-size: 15px; letter-spacing: 0.5px;
    text-transform: uppercase;
  }
  .divider {
    position: absolute; left: 232px; top: 28px; bottom: 28px;
    width: 1px; background: var(--rule);
  }
  .details {
    position: absolute; left: 255px; top: 30px; right: 18px;
    color: var(--grey); font-size: 12.5px; line-height: 1.45;
  }
  .person-name { color: var(--cyan); font-weight: 600; font-size: 17px; line-height: 1.2; }
  .person-role { font-size: 11.5px; margin-bottom: 12px; }
  .company-name { color: var(--cyan); font-weight: 600; font-size: 13.5px; }
  .address { margin-bottom: 12px; }
  .contact-list { list-style: none; color: var(--ink); font-size: 12.5px; }
  .contact-list li { display: flex; align-items: center; gap: 8px; height: 19px; }
  .contact-list svg { width: 11px; height: 11px; flex: none; fill: none; stroke: var(--navy); stroke-width: 1.6; }
  .contact-list .no-icon { padding-left: 0; }
  /* logo side */
  .card-logo {
    display: flex; align-items: center; justify-content: center; gap: 14px;
  }
  .logo-square { width: 56px; height: 56px; background: var(--navy); }
  .logo-name {
    color: var(--cyan); font-weight: 700; font-size: 24px; line-height: 1.05;
    text-transform: uppercase; letter-spacing: 0.3px;
  }
</style>
</head>
<body>
<main class="canvas">
  <section class="card card-contact">
    <div class="brand-block">
      <div class="brand-square"></div>
      <div class="brand-caption">Orin Vantage</div>
    </div>
    <div class="divider"></div>
    <div class="details">
      <p class="person-name">Clara Jo Tsang VP,</p>
      <p class="person-role">APAC M&amp;A Operations</p>
      <p class="company-name">Orin Vantage Asia Pacific Ltd</p>
      <p class="address">Unit 1407, K18 18 Tai Lok Shan<br>Road, Hong Kong</p>
      <ul class="contact-list">
        <li><svg viewBox="0 0 12 12"><rect x="3" y="1" width="6" height="10" rx="1"/></svg>+852 6038 1742</li>
        <li><svg viewBox="0 0 12 12"><path d="M2 1.5 L4.5 1.5 L5.5 4 L4 5 Q5 7.5 7 8 L8 6.5 L10.5 7.5 L10.5 10 Q5 10.5 2 5 Z" fill="#0f2d4a" stroke="none"/></svg>+852 2836 4100</li>
        <li><svg viewBox="0 0 12 12"><rect x="1.5" y="5" width="9" height="5.5"/><rect x="3.5" y="1.5" width="5" height="3.5"/></svg>+852 2836 4177</li>
        <li><svg viewBox="0 0 12 12"><rect x="1" y="2.5" width="10" height="7"/><path d="M1 2.5 L6 6.5 L11 2.5"/></svg>cjtsang@orinvantage.com</li>
        <li class="no-icon">VOIP: 4158</li>
      </ul>
    </div>
  </section>

  <section class="card card-logo">
    <div class="logo-square"></div>
    <div class="logo-name">Orin Vantage<br>Asia Pacific Ltd</div>
  </section>
</main>
</body>
</html>
```